Birchpoint Studio Complementary Pass

I’d like a complimentary pass for any 30-minute Birchpoint Studio session. Choose one of the following options: Infrared Sauna with Red Light, Massage Chair Veltrafix Compression Therapy, or Paraffin Wax Hand Bath.

Please incorporate the logo and brand colors into your design. I’d like a square image that will be printed on square business cards (no rectangles).

Please refer to the logo and menu for more details.

Contact Information for Business Card

See discretion

```html
<!DOCTYPE html>
<html lang="en">
<head>
<meta charset="utf-8">
<title>Lumora Physical Therapy – Square Cards</title>
<link rel="stylesheet" href="https://fonts.googleapis.com/css2?family=Lato:wght@400;700&display=swap">
<style>
  :root {
    --purple: #4a2d8f;
    --orange: #f0664a;
    --white: #ffffff;
    --ink: #1e1e24;
    --backdrop: #c4c5c7;
  }
  * { box-sizing: border-box; margin: 0; padding: 0; }
  html, body { width: 1200px; height: 900px; overflow: hidden; }
  body {
    background: var(--backdrop);
    font-family: "Lato", sans-serif;
    position: relative;
  }
  .card {
    position: absolute;
    top: 219px;
    width: 474px;
    height: 474px;
    background: var(--white);
    overflow: hidden;
  }
  .card--pass { left: 112px; }
  .card--contact { left: 627px; }

  .brand {
    position: absolute;
    left: 0; right: 0;
    text-align: center;
    color: var(--purple);
    font-weight: 700;
  }
  .brand__dot {
    display: block;
    margin: 0 auto;
    width: 60px; height: 60px;
    border-radius: 50%;
    background: var(--orange);
  }
  .brand__name {
    display: block;
    font-size: 56px;
    line-height: 1;
    margin-top: 24px;
    letter-spacing: 0.5px;
  }
  .brand__tagline {
    display: block;
    font-size: 16px;
    line-height: 1;
    letter-spacing: 3px;
    margin-top: 22px;
  }
  .card--pass .brand { top: 14px; }
  .card--contact .brand { top: 26px; }
  .card--contact .brand__name { margin-top: 12px; }
  .card--contact .brand__tagline { margin-top: 15px; }

  .offer {
    position: absolute;
    left: 0; right: 0; bottom: 0;
    height: 265px;
    background: var(--purple);
    color: var(--white);
    text-align: center;
    padding: 14px 20px 0;
  }
  .offer__title {
    color: var(--orange);
    font-weight: 700;
    font-size: 36px;
    line-height: 1.18;
  }
  .offer__list {
    list-style: none;
    margin-top: 12px;
    font-size: 22px;
    line-height: 1.42;
  }
  .offer__list li::before { content: "\2022\00a0"; }

  .person {
    position: absolute;
    top: 196px; left: 0; right: 0;
    text-align: center;
  }
  .person__name {
    color: var(--orange);
    font-weight: 700;
    font-size: 34px;
    line-height: 1.1;
  }
  .person__role {
    color: var(--ink);
    font-size: 22px;
    margin-top: 2px;
  }

  .icon-row {
    position: absolute;
    top: 271px; left: 78px; right: 78px;
    display: flex;
    align-items: center;
    gap: 8px;
  }
  .icon-row__rule { flex: 1; height: 2px; background: var(--orange); }
  .icon-row svg { width: 33px; height: 33px; display: block; }

  .contact-lines {
    position: absolute;
    top: 312px; left: 0; right: 0;
    text-align: center;
    color: var(--ink);
    font-size: 19px;
    line-height: 1.25;
  }
  .divider {
    position: absolute;
    top: 391px; left: 54px; right: 52px;
    height: 2px;
    background: var(--ink);
  }
  .address {
    position: absolute;
    top: 396px; left: 0; right: 0;
    text-align: center;
    color: var(--ink);
    font-size: 19px;
    line-height: 1.42;
  }
  .footer-band {
    position: absolute;
    left: 0; bottom: 0;
    width: 474px; height: 16px;
    display: block;
  }
</style>
</head>
<body>
  <section class="card card--pass">
    <div class="brand">
      <span class="brand__dot"></span>
      <span class="brand__name">Lumora</span>
      <span class="brand__tagline">PHYSICAL THERAPY</span>
    </div>
    <div class="offer">
      <h1 class="offer__title">30-minute Birchpoint Studio session.</h1>
      <ul class="offer__list">
        <li>Infrared Sauna with Red Light,</li>
        <li>Massage Chair Veltrafix Compression Therapy,</li>
        <li>Paraffin Wax Hand Bath.</li>
      </ul>
    </div>
  </section>

  <section class="card card--contact">
    <div class="brand">
      <span class="brand__dot"></span>
      <span class="brand__name">Lumora</span>
      <span class="brand__tagline">PHYSICAL THERAPY</span>
    </div>
    <div class="person">
      <h2 class="person__name">MARCUS HALE</h2>
      <p class="person__role">Managing Director</p>
    </div>
    <div class="icon-row">
      <span class="icon-row__rule"></span>
      <svg viewBox="0 0 32 32" aria-label="Phone">
        <circle cx="16" cy="16" r="16" fill="var(--purple)"/>
        <path d="M11 8.5l3 3-1.8 2.2c1 2 2.6 3.6 4.6 4.6l2.2-1.8 3 3-2 2.3c-5.5-.8-10.6-5.9-11.3-11.3z" fill="var(--white)"/>
      </svg>
      <svg viewBox="0 0 32 32" aria-label="Email">
        <circle cx="16" cy="16" r="16" fill="var(--purple)"/>
        <rect x="8.5" y="10.5" width="15" height="11" rx="1" fill="none" stroke="var(--white)" stroke-width="2"/>
        <path d="M9 11.5l7 5.5 7-5.5" fill="none" stroke="var(--white)" stroke-width="2"/>
      </svg>
      <svg viewBox="0 0 32 32" aria-label="Website">
        <circle cx="16" cy="16" r="16" fill="var(--purple)"/>
        <circle cx="16" cy="16" r="8" fill="none" stroke="var(--white)" stroke-width="2"/>
        <ellipse cx="16" cy="16" rx="3.5" ry="8" fill="none" stroke="var(--white)" stroke-width="1.6"/>
        <path d="M8 16h16" stroke="var(--white)" stroke-width="1.6"/>
      </svg>
      <span class="icon-row__rule"></span>
    </div>
    <div class="contact-lines">
      <p>044-555 018 274</p>
      <p>hello@lumorapt.com</p>
      <p>www.lumorapt.com</p>
    </div>
    <div class="divider"></div>
    <div class="address">
      <p>38, Alder Row Suite 2</p>
      <p>72190, Eastvale</p>
    </div>
    <svg class="footer-band" viewBox="0 0 474 16" preserveAspectRatio="none" aria-hidden="true">
      <polygon points="4,0 220,0 246,16 4,16" fill="var(--purple)"/>
      <polygon points="232,0 474,0 474,16 258,16" fill="var(--orange)"/>
    </svg>
  </section>
</body>
</html>
```